holloway paving service

Needs to have phone number 0418259730 and email markholloway@brightmail.com.au.
ABN 62318470915
name mark holloway

For all your concreting solutions
Excavation
Exposed & colour concrete
House & shed slabs
Driveways
Landing & steps

Contact Information for Business Card

ph 0418259730
email markholloway@brightmail.com.au.
ABN 62318470915
name mark holloway

```html
<!DOCTYPE html>
<html lang="en">
<head>
<meta charset="utf-8">
<title>Holloway Paving Service – Business Cards</title>
<link rel="stylesheet" href="https://fonts.googleapis.com/css2?family=Roboto:wght@400;500;700&family=Roboto+Condensed:wght@400;700&display=swap">
<style>
  :root {
    --page-bg: #e9e6e1;
    --card-white: #ffffff;
    --brand-orange: #f26a21;
    --ink-grey: #4d4d4f;
    --ink-light: #ffffff;
    --card-shadow: rgba(0, 0, 0, 0.18);
  }
  * { box-sizing: border-box; margin: 0; padding: 0; }
  html, body {
    width: 1200px;
    height: 950px;
    overflow: hidden;
    background: var(--page-bg);
    font-family: "Roboto", Arial, sans-serif;
  }
  .sheet {
    position: relative;
    width: 1200px;
    height: 950px;
  }
  .card {
    position: absolute;
    width: 560px;
    height: 320px;
    box-shadow: 0 6px 18px var(--card-shadow);
  }

  /* Front: white card */
  .card--front {
    left: 320px;
    top: 100px;
    background: var(--card-white);
    display: flex;
    flex-direction: column;
    align-items: center;
    justify-content: center;
    text-align: center;
  }
  .brand-mark {
    display: flex;
    align-items: center;
    gap: 10px;
    margin-bottom: 26px;
  }
  .brand-mark__square {
    width: 22px;
    height: 22px;
    background: var(--brand-orange);
  }
  .brand-mark__name {
    font-family: "Roboto Condensed", Arial, sans-serif;
    font-weight: 700;
    font-size: 22px;
    letter-spacing: 1px;
    text-transform: uppercase;
    color: var(--ink-grey);
  }
  .person-name {
    font-family: "Roboto Condensed", Arial, sans-serif;
    font-weight: 700;
    font-size: 30px;
    letter-spacing: 0.5px;
    text-transform: uppercase;
    color: var(--brand-orange);
    margin-bottom: 8px;
  }
  .contact-line {
    font-family: "Roboto Condensed", Arial, sans-serif;
    font-weight: 700;
    font-size: 17px;
    letter-spacing: 0.5px;
    text-transform: uppercase;
    color: var(--ink-grey);
    line-height: 1.45;
  }

  /* Back: orange card */
  .card--back {
    left: 320px;
    top: 520px;
    background: var(--brand-orange);
    color: var(--ink-light);
    padding: 34px 38px 30px;
  }
  .card--back .brand-mark {
    position: absolute;
    left: 38px;
    top: 38px;
    margin: 0;
  }
  .card--back .brand-mark__square { background: var(--ink-light); }
  .card--back .brand-mark__name { color: var(--ink-light); }

  .company-block {
    position: absolute;
    left: 38px;
    top: 100px;
    width: 300px;
  }
  .rule {
    display: block;
    height: 2px;
    background: var(--ink-light);
  }
  .company-block .rule--top { width: 230px; margin-bottom: 14px; }
  .company-name {
    font-family: "Roboto Condensed", Arial, sans-serif;
    font-weight: 700;
    font-size: 25px;
    letter-spacing: 0.5px;
    text-transform: uppercase;
  }
  .company-sub {
    display: flex;
    align-items: center;
    gap: 10px;
    margin-top: 2px;
  }
  .company-sub .rule { flex: 0 0 34px; height: 2px; }
  .company-sub .rule--long { flex: 1 1 auto; }
  .company-sub__word {
    font-family: "Roboto Condensed", Arial, sans-serif;
    font-size: 20px;
    letter-spacing: 3px;
    text-transform: uppercase;
  }
  .phone {
    font-family: "Roboto Condensed", Arial, sans-serif;
    font-size: 19px;
    letter-spacing: 2px;
    margin-top: 2px;
  }
  .services {
    position: absolute;
    left: 38px;
    bottom: 30px;
    font-family: "Roboto Condensed", Arial, sans-serif;
    font-size: 16px;
    line-height: 1.5;
  }
</style>
</head>
<body>
<main class="sheet">

  <section class="card card--front" aria-label="Business card front">
    <div class="brand-mark">
      <span class="brand-mark__square"></span>
      <span class="brand-mark__name">Holloway</span>
    </div>
    <h1 class="person-name">Mark Holloway</h1>
    <p class="contact-line">markholloway@brightmail.com.au</p>
    <p class="contact-line">ABN 62318470915</p>
  </section>

  <section class="card card--back" aria-label="Business card back">
    <div class="brand-mark">
      <span class="brand-mark__square"></span>
      <span class="brand-mark__name">Holloway</span>
    </div>
    <div class="company-block">
      <span class="rule rule--top"></span>
      <h2 class="company-name">Holloway Paving</h2>
      <div class="company-sub">
        <span class="rule"></span>
        <span class="company-sub__word">Service</span>
        <span class="rule rule--long"></span>
      </div>
      <p class="phone">0418259730</p>
    </div>
    <p class="services">
      Excavation | Exposed &amp; colour concrete<br>
      House &amp; shed slabs | Driveways | Landing &amp; steps
    </p>
  </section>

</main>
</body>
</html>
```